Veltrano.co - Polar Expeditions Specialists

We need a modern, visually striking business card for Veltrano.co, a company specialized in selling expedition cruises to the most remote regions on Earth, with a focus on the Arctic and Antarctica. The design should instantly communicate that the cardholder is an expert in polar travel. Use clean, premium aesthetics with cool tones like icy blue and white, possibly incorporating polar imagery (ice, glaciers, penguins, etc.)

Attached the logo

Contact Information for Business Card

Feels high-end and trustworthy.. Visually memorable — encourages people to keep it

Colors
0054AA
0677BA
7BADD7
CADEEF
E8F1F8

Requirements
Must have
• ice, glaciers, penguins, montains
Nice to have
• modern, transparente,

```html
<!DOCTYPE html>
<html lang="en">
<head>
<meta charset="utf-8">
<title>Veltrano.co – Business Card</title>
<link rel="stylesheet" href="https://fonts.googleapis.com/css2?family=Poppins:wght@300;400;600;700&display=swap">
<style>
  :root {
    --brand-blue: #3375b5;
    --deep-blue: #0054aa;
    --mid-blue: #0677ba;
    --sky-blue: #7badd7;
    --ice-light: #e8f1f8;
    --ice-mid: #cadeef;
    --ice-grey: #b4c2cd;
    --water: #9fb1bf;
    --paper: #ffffff;
    --ink: #3a3a3a;
    --backdrop: #eceff2;
  }
  * { box-sizing: border-box; margin: 0; padding: 0; }
  html, body {
    width: 1200px; height: 1000px; overflow: hidden;
    background: var(--backdrop);
    font-family: "Poppins", sans-serif;
  }
  .card {
    position: absolute;
    width: 694px; height: 398px;
    border-radius: 21px;
    overflow: hidden;
  }
  .card-front {
    left: 248px; top: 45px;
    background: var(--brand-blue);
    display: flex; align-items: center; justify-content: center;
  }
  .front-wordmark {
    color: var(--paper);
    font-weight: 600;
    font-size: 40px;
    letter-spacing: 0.5px;
  }
  .card-back {
    left: 253px; top: 508px;
    background: var(--paper);
  }
  .glacier-scene {
    position: absolute;
    left: 0; top: 225px; width: 460px; height: 173px;
    background:
      linear-gradient(90deg, rgba(255,255,255,0) 70%, var(--paper) 100%),
      linear-gradient(180deg, var(--paper) 0%, var(--ice-light) 22%, #dfe7ee 42%, var(--ice-grey) 62%, #d6dfe6 74%, var(--water) 100%);
  }
  .brand-panel {
    position: absolute;
    left: 430px; top: 55px; width: 264px; height: 343px;
    background:
      radial-gradient(ellipse at 70% 85%, var(--sky-blue) 0%, rgba(123,173,215,0) 45%),
      linear-gradient(160deg, var(--brand-blue) 0%, var(--mid-blue) 60%, var(--deep-blue) 100%);
    border-top-left-radius: 190px 150px;
    border-top-right-radius: 40px 30px;
    box-shadow: inset 8px 10px 14px rgba(0, 30, 70, 0.35);
  }
  .contact-block {
    position: absolute;
    left: 90px; top: 46px; width: 216px;
    text-align: center;
    color: var(--ink);
  }
  .brand-row {
    display: flex; align-items: center; justify-content: center; gap: 6px;
    margin-bottom: 27px;
  }
  .brand-dot {
    width: 30px; height: 30px; border-radius: 50%;
    background: var(--brand-blue); flex: none;
  }
  .brand-text { display: flex; flex-direction: column; align-items: center; }
  .brand-name {
    color: var(--brand-blue);
    font-weight: 600; font-size: 25px; line-height: 1.05;
  }
  .brand-tagline {
    color: var(--brand-blue);
    font-weight: 600; font-size: 7.5px; margin-top: 2px;
  }
  .holder-name {
    color: var(--brand-blue);
    font-weight: 600; font-size: 19px; line-height: 1.1;
  }
  .holder-position {
    color: var(--brand-blue);
    font-size: 10px; letter-spacing: 2px; margin-top: 2px;
  }
  .contact-icons {
    display: flex; justify-content: center; gap: 2px;
    margin: 6px 0 4px;
  }
  .contact-icons svg { width: 25px; height: 25px; }
  .contact-lines {
    font-weight: 300; font-size: 16px; line-height: 18px;
  }
</style>
</head>
<body>
  <section class="card card-front">
    <span class="front-wordmark">Veltrano.co</span>
  </section>

  <section class="card card-back">
    <div class="glacier-scene" role="img" aria-label="Photo of glaciers and icebergs on calm polar water"></div>
    <div class="brand-panel" role="img" aria-label="Large paper-cut brand decoration in icy blue"></div>

    <div class="contact-block">
      <div class="brand-row">
        <span class="brand-dot"></span>
        <span class="brand-text">
          <span class="brand-name">Veltrano.co</span>
          <span class="brand-tagline">Polar Expeditions Specialists</span>
        </span>
      </div>
      <div class="holder-name">NAME SURNAME</div>
      <div class="holder-position">POSITION</div>
      <div class="contact-icons">
        <svg viewBox="0 0 26 26" aria-label="Phone"><circle cx="13" cy="13" r="13" fill="var(--brand-blue)"/><rect x="9" y="6" width="8" height="14" rx="1.5" fill="none" stroke="#fff" stroke-width="1.4"/><circle cx="13" cy="17.5" r="0.8" fill="#fff"/></svg>
        <svg viewBox="0 0 26 26" aria-label="Email"><circle cx="13" cy="13" r="13" fill="var(--brand-blue)"/><rect x="6.5" y="8.5" width="13" height="9" fill="none" stroke="#fff" stroke-width="1.3"/><path d="M6.5 8.5 L13 13.5 L19.5 8.5" fill="none" stroke="#fff" stroke-width="1.3"/></svg>
        <svg viewBox="0 0 26 26" aria-label="Website"><circle cx="13" cy="13" r="13" fill="var(--brand-blue)"/><circle cx="13" cy="13" r="6.5" fill="none" stroke="#fff" stroke-width="1.2"/><ellipse cx="13" cy="13" rx="3" ry="6.5" fill="none" stroke="#fff" stroke-width="1"/><path d="M6.5 13 H19.5 M7.5 10 H18.5 M7.5 16 H18.5" stroke="#fff" stroke-width="1"/></svg>
      </div>
      <div class="contact-lines">
        <div>(123) 456-7890</div>
        <div>name@website.com</div>
        <div>website.com</div>
      </div>
    </div>
  </section>
</body>
</html>
```